Moxy Fen needs some awesome stationary

Do you have what it takes to get my brand? You either do or you don't, have a crack at a design and you my just win my business.

I don't want to waste your or my time, so put your creative genius on either a business card or envelope.

I however need a package of stationary that follows the same brand. I will message you to complete the remaining should I like your first submission.

Here is what I need, have a go!

Basically I need the following for my small business based in melbourne.
- Letterhead (printer ready and MS Word)
- Business Card
- Compliments Slip
- Envelope
- Proposal Cover Page (MS Word only)
- Presentation Folder
- Marbled Fox Cards
- Student Name Tent
- Index Cards
- Vell-Ka

I am establishing the brand and it must be modern, professional but also relaxed; that is not formal and not corporate. It represents a company are leaders, but small enough to care and operate like a bunch of friends. We are bringing people and conversations back to business, and turfing out all the bureaucracy and crazy and wasteful procedures. Its about "lets talk and figure it out together and find even better ways".

Target Market(s)

Mainly companies that build software products, but Agile practices are used in many other industries (even graphic design projects)

Industry/Entity Type

Information Technology

Font styles to use
Sans Serif

Colors
3176b5
aaaaaa

Requirements
Must have
• I like curves and circles and not boxes or rectangles.
• I want a colour rich design with my brand colours, but it must be balanced.
• I want more modern than traditional, but simple modern
Should not have
• Not corporate
• Please don't waste my time if your not going to think about it.
• Don't mess with my primary logo
• Don't change my colours
• Don't overlay logo on image

```html
<!DOCTYPE html>
<html lang="en">
<head>
<meta charset="utf-8">
<title>Moxy Fen – Business Card</title>
<link rel="stylesheet" href="https://fonts.googleapis.com/css2?family=PT+Sans:wght@400;700&display=swap">
<style>
  :root {
    --brand-blue: #2d5ca6;
    --brand-grey: #959eac;
    --text-dark: #3a3a3a;
    --rule: #9aa4b4;
    --card-white: #ffffff;
    --backdrop: #e8e5e1;
  }
  * { box-sizing: border-box; margin: 0; padding: 0; }
  html, body {
    width: 1200px; height: 987px; overflow: hidden;
    background: var(--backdrop);
    font-family: "PT Sans", sans-serif;
  }
  .stage { position: relative; width: 1200px; height: 987px; }
  .card {
    position: absolute; left: 293px; width: 615px; height: 349px;
    border-radius: 18px; overflow: hidden;
  }
  .card--front { top: 131px; background: var(--card-white); }
  .card--back { top: 506px; background: var(--brand-blue); }

  /* front */
  .brand { position: absolute; left: 37px; top: 26px; }
  .brand__dot {
    width: 104px; height: 104px; border-radius: 50%;
    background: var(--brand-grey); margin-bottom: 8px;
  }
  .brand__name {
    font-weight: 700; font-size: 40px; line-height: 1;
    color: var(--brand-blue); letter-spacing: 0.3px;
  }
  .holder { position: absolute; right: 35px; top: 160px; text-align: right; }
  .holder__name { font-weight: 700; font-size: 21px; color: var(--brand-blue); line-height: 1.1; }
  .holder__role { font-size: 16px; color: var(--brand-grey); line-height: 1.3; }
  .divider {
    position: absolute; left: 37px; right: 35px; top: 211px;
    height: 1px; background: var(--rule);
  }
  .contacts { position: absolute; left: 37px; top: 221px; list-style: none; }
  .contacts li {
    display: flex; align-items: center; height: 23.5px;
    font-size: 16px; color: var(--text-dark);
  }
  .contacts svg { width: 14px; height: 14px; margin-right: 9px; fill: var(--brand-blue); flex: none; }
  .address {
    position: absolute; right: 35px; top: 245px; text-align: right;
    font-style: normal; font-size: 16px; line-height: 23.5px; color: var(--text-dark);
  }
  .footer-band { position: absolute; left: 0; right: 0; bottom: 0; height: 22px; display: flex; }
  .footer-band__blue { flex: 0 0 400px; background: var(--brand-blue); }
  .footer-band__grey { flex: 1; background: var(--brand-grey); }

  /* back */
  .back__circle {
    position: absolute; left: 171px; top: -172px;
    width: 444px; height: 444px; border-radius: 50%;
    background: var(--brand-grey);
  }
  .back__name {
    position: absolute; left: 0; right: 16px; top: 246px; text-align: center;
    font-weight: 700; font-size: 56px; line-height: 1; color: var(--card-white);
  }
  .back__web {
    position: absolute; left: 0; right: 16px; top: 311px; text-align: center;
    font-size: 14px; letter-spacing: 4px; color: var(--card-white);
  }
</style>
</head>
<body>
<main class="stage">

  <section class="card card--front" aria-label="Business card front">
    <div class="brand">
      <div class="brand__dot"></div>
      <div class="brand__name">Moxy Fen</div>
    </div>

    <div class="holder">
      <div class="holder__name">Dale Ornsby</div>
      <div class="holder__role">CEO, Professional Agile Trainer</div>
    </div>

    <div class="divider"></div>

    <ul class="contacts">
      <li>
        <svg viewBox="0 0 24 24" aria-hidden="true"><path d="M6.6 10.8a15.1 15.1 0 0 0 6.6 6.6l2.2-2.2c.3-.3.7-.4 1-.2 1.1.4 2.3.6 3.6.6.6 0 1 .4 1 1V20c0 .6-.4 1-1 1A17 17 0 0 1 3 4c0-.6.4-1 1-1h3.5c.6 0 1 .4 1 1 0 1.3.2 2.5.6 3.6.1.3 0 .7-.2 1z"/></svg>
        1300MOXYF
      </li>
      <li>
        <svg viewBox="0 0 24 24" aria-hidden="true"><path d="M7 1h10a2 2 0 0 1 2 2v18a2 2 0 0 1-2 2H7a2 2 0 0 1-2-2V3a2 2 0 0 1 2-2zm0 3v14h10V4zm5 15.5a1 1 0 1 0 0 2 1 1 0 0 0 0-2z"/></svg>
        +61 400 217 386
      </li>
      <li>
        <svg viewBox="0 0 24 24" aria-hidden="true"><path d="M2 5h20v14H2zm2 2v.5l8 5 8-5V7zm0 2.8V17h16V9.8l-8 5z"/></svg>
        dale@moxy-fen.com.au
      </li>
      <li>
        <svg viewBox="0 0 24 24" aria-hidden="true"><path d="M12 2a10 10 0 1 0 0 20 10 10 0 0 0 0-20zm-1 17.9A8 8 0 0 1 4.2 10L9 14.8v1c0 1.1.9 2 2 2zm6.9-2.5A2 2 0 0 0 16 16h-1v-3a1 1 0 0 0-1-1H8v-2h2a1 1 0 0 0 1-1V7h2a2 2 0 0 0 2-2v-.4a8 8 0 0 1 2.9 12.8z"/></svg>
        www.moxy-fen.com.au
      </li>
    </ul>

    <address class="address">
      PO Box 4410<br>
      Ashvale North<br>
      VIC 3990, Australia
    </address>

    <div class="footer-band">
      <div class="footer-band__blue"></div>
      <div class="footer-band__grey"></div>
    </div>
  </section>

  <section class="card card--back" aria-label="Business card back">
    <div class="back__circle"></div>
    <div class="back__name">Moxy Fen</div>
    <div class="back__web">www.moxy-fen.com.au</div>
  </section>

</main>
</body>
</html>
```